Fabrication and machining company needing printed material designs.

Heron Vessels, Inc. wants to use appealing visuals as well as informative text to tell potential clients about our capabilities in fabrication and machining. We have a new logo to showcase as well as a new website. The use of print media will allow us to leave tangible information with clients, and therefore the design will need to be concise, informative, and visually appealing.

Full Page Flyer (approx. 8.5" x 11"), front and back design. This will be a detailed offering of capabilities and services for our shop.

Half Page Flyer (approx. 5.5" x 8.5"), front and back design. An abbreviated version of the full page flyer, meant to be easily handed out and stored inside a note book.

Bi-fold business card front and back. General offerings of our services. Minimal if any details. Finished size is twice the size of a business card (approx. 4" x 3.5"), once folded in half will be the same size as a standard business card (approx. 2" x 3.5").

Please use www.heronvesselsinc.example for theme ideas. The font used for our logo is ethnocentric, not to be used for all text.

Target Market(s)

Industrial Consumers

Font styles to use
Sans Serif

```html
<!DOCTYPE html>
<html lang="en">
<head>
<meta charset="utf-8">
<title>Heron Vessels, Inc. – Card Inside</title>
<link rel="stylesheet" href="https://fonts.googleapis.com/css2?family=Mulish:ital,wght@0,400;0,800;0,900;1,800&display=swap">
<style>
  :root {
    --brand-orange: #ff4000;
    --ink: #111111;
    --paper: #ffffff;
  }
  * { margin: 0; padding: 0; box-sizing: border-box; }
  html, body { width: 1200px; height: 1050px; overflow: hidden; background: var(--paper); }
  .card {
    position: relative;
    width: 1200px;
    height: 1050px;
    background: var(--paper);
    font-family: "Mulish", sans-serif;
    color: var(--ink);
  }
  .products {
    position: absolute;
    top: 48px;
    left: 0;
    width: 1245px;
    text-align: center;
  }
  .products-title {
    color: var(--brand-orange);
    font-weight: 900;
    font-size: 60px;
    line-height: 1;
    letter-spacing: 1px;
    margin-bottom: 12px;
  }
  .products-list {
    list-style: none;
    font-size: 45px;
    font-weight: 400;
    line-height: 58px;
  }
  .specialty {
    position: absolute;
    top: 344px;
    left: 0;
    width: 1208px;
    text-align: center;
    font-style: italic;
    font-weight: 800;
    font-size: 36px;
    line-height: 51px;
  }
  .company {
    position: absolute;
    left: 50px;
    top: 600px;
    display: flex;
    align-items: center;
    gap: 20px;
  }
  .company-mark {
    width: 54px;
    height: 54px;
    background: var(--brand-orange);
  }
  .company-name {
    color: var(--brand-orange);
    font-weight: 900;
    font-size: 36px;
    letter-spacing: 0.5px;
  }
  .contact {
    position: absolute;
    left: 597px;
    top: 632px;
  }
  .contact-name {
    font-weight: 900;
    font-size: 62px;
    line-height: 1;
    letter-spacing: 0.5px;
  }
  .contact-position {
    font-size: 46px;
    font-weight: 400;
    line-height: 1;
    margin-top: 18px;
  }
  .contact-lines {
    list-style: none;
    margin-top: 50px;
    margin-left: -33px;
  }
  .contact-lines li {
    display: flex;
    align-items: center;
    gap: 10px;
    font-size: 33px;
    line-height: 45px;
  }
  .contact-lines svg { width: 38px; height: 38px; flex: none; }
  .footer-band {
    position: absolute;
    left: 597px;
    top: 998px;
    width: 603px;
    height: 52px;
    background: var(--ink);
    border-top-left-radius: 18px;
  }
</style>
</head>
<body>
<main class="card">
  <section class="products">
    <h1 class="products-title">OUR PRODUCTS</h1>
    <ul class="products-list">
      <li>Api 12-F, Api 650 SpecificationBuilt Tanks</li>
      <li>Fire Tubes/Tank Heaters I Tank Coils</li>
      <li>Walkways I Stairs I Pump Skids</li>
    </ul>
  </section>

  <p class="specialty">We specialize in API-12F &amp; API-650<br>tank manufacturing</p>

  <div class="company">
    <span class="company-mark"></span>
    <span class="company-name">HERON VESSELS, INC.</span>
  </div>

  <section class="contact">
    <h2 class="contact-name">YOUR NAME</h2>
    <p class="contact-position">Your Position</p>
    <ul class="contact-lines">
      <li>
        <svg viewBox="0 0 38 38" aria-hidden="true">
          <circle cx="19" cy="19" r="18" fill="var(--ink)"/>
          <path d="M12.5 10.5l4 -0.5 2 5 -2.5 2c1 2.5 3 4.5 5.5 5.5l2 -2.5 5 2 -0.5 4c-0.3 1 -1 1.5 -2 1.5 -8 -0.5 -14 -6.5 -14.5 -14.5 0 -1 0.5 -1.7 1 -2z" fill="var(--paper)"/>
        </svg>
        (555) 014 - 2698
      </li>
      <li>
        <svg viewBox="0 0 38 38" aria-hidden="true">
          <circle cx="19" cy="19" r="18" fill="var(--ink)"/>
          <rect x="10" y="12.5" width="18" height="13" fill="none" stroke="var(--paper)" stroke-width="2"/>
          <path d="M10 12.5l9 7 9 -7" fill="none" stroke="var(--paper)" stroke-width="2"/>
        </svg>
        youremail@heronvesselsinc.example
      </li>
    </ul>
  </section>

  <div class="footer-band"></div>
</main>
</body>
</html>
```